Executive recruiting firm in need of business card design

Executive recruiting firm looking for a sleek, classy and modern business card design; card itself will be square shape, rounded edges and soft touch paper, our colors are dark blues in the navy color scale, silvers and grays. Reference our website for a better idea of our company's feel and goals at Tarvex-Up.com - our company message is "Employee Engagement Begins at Recruitment" this should be on the card

```html
<!DOCTYPE html>
<html lang="en">
<head>
<meta charset="utf-8">
<title>Tarvex-Up Business Card</title>
<link href="https://fonts.googleapis.com/css2?family=Open+Sans:wght@400;600;700&display=swap" rel="stylesheet">
<style>
  :root {
    --stage: #2a2a2d;
    --navy: #1b1b6b;
    --navy-deep: #0e0f4a;
    --navy-text: #1f2060;
    --paper: #ffffff;
    --gray-text: #55575f;
    --rule: #9a9cb0;
  }
  * { box-sizing: border-box; margin: 0; padding: 0; }
  html, body { width: 1200px; height: 840px; overflow: hidden; }
  body {
    background: var(--stage);
    font-family: "Open Sans", Arial, sans-serif;
    position: relative;
  }
  .card {
    position: absolute;
    width: 620px;
    height: 354px;
    border-radius: 6px;
    overflow: hidden;
  }
  .brand-name {
    font-family: "Open Sans", Arial, sans-serif;
    font-weight: 600;
    line-height: 1;
  }
  /* Front */
  .card-front {
    left: 110px; top: 60px;
    background: linear-gradient(135deg, var(--navy) 0%, var(--navy-deep) 100%);
    color: var(--paper);
  }
  .front-brand {
    position: absolute;
    left: 0; right: 0; top: 128px;
    text-align: center;
    font-size: 40px;
    color: var(--paper);
  }
  .front-message {
    position: absolute; left: 0; right: 0; bottom: 56px;
    text-align: center;
    font-size: 15px;
    color: var(--paper);
  }
  /* Back */
  .card-back {
    left: 470px; top: 430px;
    background: var(--paper);
    color: var(--navy-text);
  }
  .edge-tab {
    position: absolute;
    left: -22px; top: 150px;
    width: 44px; height: 44px; border-radius: 50%;
    background: var(--navy);
  }
  .back-brand {
    position: absolute; right: 40px; top: 62px;
    font-size: 32px;
    color: var(--navy-text);
  }
  .person { position: absolute; left: 50px; top: 92px; }
  .person-name { font-weight: 700; font-size: 15px; letter-spacing: 0.5px; text-transform: uppercase; }
  .person-role { font-size: 14px; color: var(--gray-text); }
  .back-rule {
    position: absolute;
    left: 50px; right: 40px; top: 136px;
    height: 1px; background: var(--rule);
  }
  .address {
    position: absolute; right: 40px; top: 152px;
    text-align: right; font-size: 14px; line-height: 1.35;
    font-style: normal;
    color: var(--gray-text);
  }
  .address .web { font-weight: 700; color: var(--navy-text); }
  .contacts {
    position: absolute; left: 50px; bottom: 34px;
    list-style: none; font-size: 14px; color: var(--gray-text);
  }
  .contacts li { display: flex; align-items: center; gap: 10px; line-height: 1.45; }
  .contacts svg { width: 13px; height: 13px; fill: var(--navy-text); }
</style>
</head>
<body>
  <section class="card card-front">
    <p class="brand-name front-brand">Tarvex-Up</p>
    <p class="front-message">Employee Engagement Begins at Recruitment</p>
  </section>

  <section class="card card-back">
    <span class="edge-tab"></span>
    <p class="brand-name back-brand">Tarvex-Up</p>
    <div class="person">
      <p class="person-name">Dana Whitfield</p>
      <p class="person-role">CEO/FOUNDER</p>
    </div>
    <div class="back-rule"></div>
    <address class="address">
      <p>48 Linden Grove Ave</p>
      <p>Marlow Hills, CA</p>
      <p class="web">www.tarvex-up.com</p>
    </address>
    <ul class="contacts">
      <li><svg viewBox="0 0 16 16" aria-hidden="true"><path d="M3 1l3 3-2 2c1 2 3 4 5 5l2-2 3 3-2 2C7 14 2 9 1 3z"/></svg>555 214 7093</li>
      <li><svg viewBox="0 0 16 16" aria-hidden="true"><path d="M4 0h8v16H4zM5 2v10h6V2z"/></svg>555 381 6247</li>
      <li><svg viewBox="0 0 16 16" aria-hidden="true"><path d="M4 1h8v4H4zM1 6h14v8H1zM4 10h8v5H4z"/></svg>555 702 4418</li>
      <li><svg viewBox="0 0 16 16" aria-hidden="true"><path d="M1 3h14v10H1zM2 4l6 5 6-5v1L8 10 2 5z"/></svg>dana@tarvex-up.com</li>
    </ul>
  </section>
</body>
</html>
```